Brantor Works Business Card

Modern and Professional Business Card for a Med size construction/development company.

See the samples below for the design I like … but I need ideas for incorporating the red company logo while still keeping the clean look of the card samples that are attached.

Logo and tag line on the back … info on the front.

Tagline: Solid Work Built from the Base Up

Target Market(s)

Med-Large General Contractors

Contact Information for Business Card

Brantor Works Limited
42 Fenwick Avenue
Mt. Pearl, NL
A1N 4R9

t: 709-555-0147
f: 709-555-0182
w: www.brantorworks-example.com

Font styles to use
Sans Serif

Colors
fbee3e

Requirements
Must have
• I like the black and yellow designs of the attached samples …. but I'm not sure how to incorporate the red Brantor Works logo into that design??
Nice to have
• Construction safety strips

```html
<!DOCTYPE html>
<html lang="en">
<head>
<meta charset="utf-8">
<title>Brantor Works Business Card</title>
<link rel="stylesheet" href="https://fonts.googleapis.com/css2?family=Arimo:wght@700&family=Lato:wght@400&family=Roboto:wght@500;700&display=swap">
<style>
  :root {
    --stage: #efefef;
    --card-red: #e41e2a;
    --card-light: #e6e6e8;
    --ink-white: #ffffff;
    --ink-dark: #1d1d1f;
    --rule-red: #e41e2a;
  }
  * { margin: 0; padding: 0; box-sizing: border-box; }
  html, body { width: 1200px; height: 900px; overflow: hidden; }
  body { background: var(--stage); position: relative; }

  .card { position: absolute; box-shadow: 0 3px 8px rgba(0,0,0,.25); }

  .card-front {
    left: 330px; top: 90px; width: 555px; height: 343px;
    background: var(--card-red); color: var(--ink-white);
    text-align: center;
    font-family: "Lato", sans-serif;
  }
  .holder-name {
    position: absolute; left: 0; right: 0; top: 60px;
    font-family: "Arimo", sans-serif; font-weight: 700;
    font-size: 19px; letter-spacing: .3px;
  }
  .holder-title {
    position: absolute; left: 0; right: 0; top: 80px;
    font-size: 15.5px;
  }
  .contact-icons { position: absolute; left: 187px; top: 107px; }
  .contact-lines {
    position: absolute; left: 0; right: 0; top: 141px;
    font-size: 16px; line-height: 20.5px;
  }
  .divider {
    position: absolute; left: 187px; width: 180px; top: 211px;
    height: 1px; background: var(--ink-white);
  }
  .address-lines {
    position: absolute; left: 0; right: 0; top: 222px;
    font-size: 16px; line-height: 20px;
  }

  .card-back {
    left: 330px; top: 470px; width: 558px; height: 342px;
    background: var(--card-light);
  }
  .company-mark {
    position: absolute; left: 0; right: 0; top: 100px;
    text-align: center;
    font-family: "Roboto", sans-serif; font-weight: 700;
    font-size: 38px; line-height: 44px; letter-spacing: 1px;
    color: var(--rule-red);
  }
  .tagline {
    position: absolute; left: 140px; width: 279px; top: 259px;
    height: 35px;
    border-top: 3px solid var(--rule-red);
    border-bottom: 3px solid var(--rule-red);
    font-family: "Roboto", sans-serif; font-weight: 500;
    font-size: 14.5px; line-height: 29px; color: var(--ink-dark);
    text-align: center; white-space: nowrap; letter-spacing: 0;
  }
</style>
</head>
<body>
  <section class="card card-front">
    <div class="holder-name">DANIEL HARTLEY</div>
    <div class="holder-title">Managing Director</div>
    <svg class="contact-icons" width="180" height="24" viewBox="0 0 180 24" aria-hidden="true">
      <line x1="0" y1="12" x2="50" y2="12" stroke="#fff" stroke-width="1"/>
      <line x1="130" y1="12" x2="180" y2="12" stroke="#fff" stroke-width="1"/>
      <circle cx="65" cy="12" r="11" fill="#fff"/>
      <path d="M58 10 q7 -6 14 0 l-2 2 h-3 v-2 h-4 v2 h-3 z M60 13 h10 v4 h-10 z" fill="#e41e2a"/>
      <circle cx="90" cy="12" r="11" fill="#fff"/>
      <rect x="83" y="7" width="14" height="10" fill="none" stroke="#e41e2a" stroke-width="1.6"/>
      <path d="M83 7 L90 13 L97 7" fill="none" stroke="#e41e2a" stroke-width="1.6"/>
      <circle cx="115" cy="12" r="11" fill="#fff"/>
      <circle cx="115" cy="12" r="6.5" fill="none" stroke="#e41e2a" stroke-width="1.6"/>
      <path d="M108.5 12 h13 M115 5.5 q-4 6.5 0 13 M115 5.5 q4 6.5 0 13" fill="none" stroke="#e41e2a" stroke-width="1.2"/>
    </svg>
    <div class="contact-lines">
      <div>709-555-0147</div>
      <div>709-555-0182</div>
      <div>www.brantorworks-example.com</div>
    </div>
    <div class="divider"></div>
    <div class="address-lines">
      <div>Brantor Works Limited</div>
      <div>42 Fenwick Avenue</div>
      <div>Kestrel Bay, NL A0B 2C4</div>
    </div>
  </section>

  <section class="card card-back">
    <div class="company-mark">BRANTOR WORKS<br>LIMITED</div>
    <div class="tagline">SOLID WORK BUILT FROM THE BASE UP</div>
  </section>
</body>
</html>
```